Business Card Design - Photographer

I am a landscape photographer and I require a business card design. 

I require two designs:
1)  a double sided business card
 and
b)  a single sided business card 

The single sided design can either be the same as the double sided (with just one side having all the information)....or it can be an entire new design. Its up to you.

My corporate colours are (CMYK):

Blue   69, 32, 0, 0
Grey  72,  64,  47,  31
Green  32,  2,  91,  0
Yellow   0, 19, 92, 0
Orange  0, 39, 75, 0

Colour space in final file should be in CMYK.

The details that need to be included on the card:

- Use the provided Logo
- Name: Wiktor Baranowski
- Email:   sales@vistalumeworks.com.au
- Website:    vistalumeworks.com.au
- Twitter:    twitter.com/vistalumeworks
- Facebook:   facebook.com/vistalumeworks
- Mobile  0417 539 662

Please use the attached template to design the logo to the specified size, including the marked bleed lines. I have also attached my logo in PNG (transparent background) and ai format for you to use.

The final file should be:
- Photoshop version with layers so I can edit the name/text etc. All non vector files should be high resolution at 1039 x 697 pixels at 300 dpi.

I also require a file as:
- Vector based PDF

Anyway questions please contact me.

Thank you

Industry/Entity Type

Landscape

Logo styles of interest
Pictorial/Combination Logo
Abstract Logo
Wordmark Logo
Lettermark Logo
Requirements
Must have
• The details that need to be included on the card:

- Use the provided Logo
- Name: Wiktor Baranowski
- Email: sales@vistalumeworks.com.au
- Website: vistalumeworks.com.au
- Twitter: twitter.com/vistalumeworks
- Facebook: facebook.com/vistalumeworks
- Mobile 0417 539 662

```html
<!DOCTYPE html>
<html lang="en">
<head>
<meta charset="utf-8">
<title>Vistalume Works – Business Card</title>
<link rel="stylesheet" href="https://fonts.googleapis.com/css2?family=Cinzel:wght@600&family=Open+Sans:wght@400;600&display=swap">
<style>
  :root {
    --bg: #ecebe8;
    --card-white: #ffffff;
    --slate: #3f4559;
    --slate-text: #4a4f62;
    --blue: #4f9ad5;
    --green: #b5d334;
    --rule: #c9cbd1;
    --light: #ffffff;
  }
  * { box-sizing: border-box; margin: 0; padding: 0; }
  html, body { width: 1200px; height: 758px; overflow: hidden; background: var(--bg); }
  .canvas { position: relative; width: 1200px; height: 758px; }
  .card {
    position: absolute; top: 219px; width: 520px; height: 320px;
    border-radius: 26px; overflow: hidden;
    box-shadow: 0 6px 18px rgba(0,0,0,.18);
  }
  .card--front { left: 60px; background: var(--card-white); }
  .card--back { left: 620px; background: var(--slate); }

  .front__swoosh { position: absolute; inset: 0; width: 520px; height: 320px; }

  .brand { position: absolute; left: 26px; top: 62px; width: 210px; text-align: center; }
  .brand__dot { display: block; width: 58px; height: 58px; border-radius: 50%; background: var(--slate); margin: 0 auto 12px; }
  .brand__name { font-family: "Cinzel", serif; font-weight: 600; font-size: 19px; letter-spacing: .5px; color: var(--slate); white-space: nowrap; }

  .divider { position: absolute; left: 252px; top: 28px; width: 1px; height: 150px; background: var(--rule); }

  .contacts { position: absolute; left: 266px; top: 24px; list-style: none; font-family: "Open Sans", sans-serif; font-size: 13px; color: var(--slate-text); }
  .contacts__name { font-weight: 600; font-size: 14px; color: var(--slate); height: 28px; line-height: 28px; }
  .contacts li { display: flex; align-items: center; gap: 7px; height: 24px; white-space: nowrap; }
  .contacts svg { width: 11px; height: 11px; flex: none; }
  .icon-square { width: 10px; height: 10px; flex: none; border-radius: 2px; }
  .icon-square--blue { background: var(--blue); }
  .icon-square--slate { background: var(--slate); }

  .address { position: absolute; left: 40px; top: 262px; font-family: "Open Sans", sans-serif; font-size: 13px; line-height: 19px; color: var(--light); }

  .back__brand { position: absolute; left: 0; right: 0; top: 110px; text-align: center; font-family: "Cinzel", serif; font-weight: 600; font-size: 30px; letter-spacing: 1px; color: var(--light); }
  .back__web { position: absolute; left: 0; right: 0; top: 245px; text-align: center; font-family: "Cinzel", serif; font-weight: 600; font-size: 17px; letter-spacing: 1px; color: var(--light); }
</style>
</head>
<body>
<main class="canvas">
  <section class="card card--front" aria-label="Business card front, complete single-sided version">
    <svg class="front__swoosh" viewBox="0 0 520 320" aria-hidden="true">
      <path d="M0 320 L0 246 C120 222 260 236 360 256 C430 270 490 282 520 286 L520 320 Z" fill="var(--slate)"/>
      <path d="M0 234 C90 212 190 204 290 214" fill="none" stroke="var(--slate)" stroke-width="4"/>
      <path d="M120 236 C260 226 400 250 520 254" fill="none" stroke="var(--green)" stroke-width="2"/>
      <path d="M300 246 C400 246 470 236 520 222" fill="none" stroke="var(--blue)" stroke-width="6"/>
    </svg>

    <div class="brand">
      <span class="brand__dot"></span>
      <p class="brand__name">Vistalume Works</p>
    </div>

    <span class="divider"></span>

    <ul class="contacts">
      <li class="contacts__name">Wiktor Baranowski</li>
      <li><svg viewBox="0 0 12 12"><rect x="3" y="0.5" width="6" height="11" rx="1.2" fill="var(--slate)"/><rect x="4.2" y="2" width="3.6" height="6" fill="#fff"/></svg>0417 539 662</li>
      <li><svg viewBox="0 0 12 12"><rect x="0.5" y="2" width="11" height="8" rx="1" fill="var(--slate)"/><path d="M1 2.5 L6 6.5 L11 2.5" fill="none" stroke="#fff" stroke-width="1"/></svg>sales@vistalumeworks.com.au</li>
      <li><svg viewBox="0 0 12 12"><circle cx="6" cy="6" r="5" fill="var(--slate)"/></svg>www.vistalumeworks</li>
      <li><span class="icon-square icon-square--blue"></span>vistalumeworks</li>
      <li><span class="icon-square icon-square--slate"></span>vistalumeworks</li>
    </ul>

    <p class="address">00, Complex name, state<br>city 0020</p>
  </section>

  <section class="card card--back" aria-label="Business card back">
    <p class="back__brand">Vistalume Works</p>
    <p class="back__web">www.vistalumeworks.com.au</p>
  </section>
</main>
</body>
</html>
```